Parcelwise HQ letterhead and envelope

Design a formal (8.5x11) letterhead and envelope for sales outreach and legal matters. Using design input from https://www.parcelwisehq.example/ and the attached documents.

Industry/Entity Type

Software Service

Requirements
Must have
• These 4 hex colors are our official colors:
• #355c98 [blue]
• #1eb1a2 [teal]
• #fdba12 [gold]
• #f1653b [orange]
• So no other colors besides these should be used.

```html
<!DOCTYPE html>
<html lang="en">
<head>
<meta charset="utf-8">
<title>Parcelwise HQ Letterhead</title>
<link href="https://fonts.googleapis.com/css2?family=Lato:wght@400;700&family=Yellowtail&display=swap" rel="stylesheet">
<style>
  :root {
    --brand-blue: #355c98;
    --brand-teal: #1eb1a2;
    --brand-gold: #fdba12;
    --brand-orange: #f1653b;
    --paper: #ffffff;
    --paper-shade: #f4f4f5;
    --ink: #505256;
    --ink-dark: #2f3033;
  }
  * { box-sizing: border-box; margin: 0; padding: 0; }
  html, body { width: 996px; height: 1200px; overflow: hidden; }
  body { background: var(--paper); font-family: "Lato", sans-serif; }

  .letterhead {
    position: relative;
    width: 996px;
    height: 1200px;
    background: linear-gradient(160deg, var(--paper) 0%, var(--paper-shade) 55%, var(--paper) 100%);
    overflow: hidden;
  }

  .icon-pattern {
    position: absolute;
    left: 0; top: 110px;
    width: 996px; height: 990px;
    background:
      radial-gradient(circle at 88% 18%, rgba(241,101,59,0.08), transparent 12%),
      radial-gradient(circle at 20% 12%, rgba(253,186,18,0.08), transparent 10%),
      radial-gradient(circle at 75% 70%, rgba(241,101,59,0.06), transparent 10%),
      radial-gradient(circle at 88% 88%, rgba(30,177,162,0.07), transparent 10%);
  }

  .brand {
    position: absolute;
    left: 30px; top: 44px;
    display: flex; align-items: center; gap: 14px;
  }
  .brand-dot {
    width: 46px; height: 46px;
    border: 4px solid var(--brand-blue);
    border-radius: 50%;
  }
  .brand-name {
    font-size: 44px; font-weight: 400;
    color: var(--brand-blue);
    letter-spacing: 0.5px;
  }

  .address {
    position: absolute;
    left: 753px; top: 50px;
    padding-left: 12px;
    border-left: 1px solid #b9bcc2;
    font-family: Arial, sans-serif;
    font-size: 15px; line-height: 20px;
    color: var(--ink-dark);
  }
  .address-line { display: flex; align-items: center; gap: 5px; }
  .address-line.indent { padding-left: 19px; }

  .letter-body {
    position: absolute;
    left: 84px; top: 326px;
    width: 828px;
  }
  .salutation {
    font-size: 18px; font-weight: 700;
    color: var(--brand-blue);
    margin-bottom: 22px;
  }
  .letter-body p.copy {
    font-size: 17.5px; line-height: 27px;
    color: var(--ink);
    text-align: justify;
    margin-bottom: 22px;
  }
  .closing {
    margin-top: 18px;
    font-size: 20px;
    color: var(--ink-dark);
  }
  .signature {
    font-family: "Yellowtail", cursive;
    font-size: 38px;
    color: var(--brand-blue);
    margin-top: 2px;
  }

  .footer {
    position: absolute;
    left: 0; top: 1112px;
    width: 996px; height: 62px;
  }
  .footer-rule {
    position: absolute; left: 0; width: 996px; height: 2px;
    background: var(--brand-teal);
  }
  .footer-rule.top { top: 0; }
  .footer-rule.bottom { top: 58px; }
  .footer-band {
    position: absolute; left: 0; top: 6px;
    width: 996px; height: 48px;
    background: var(--brand-blue);
    display: flex; align-items: center;
    padding-left: 70px; gap: 12px;
    font-family: Arial, sans-serif;
    font-size: 15px; color: var(--paper);
  }
  .contact-item { display: flex; align-items: center; gap: 5px; }
  .footer-seal {
    position: absolute;
    left: 842px; top: -20px;
    width: 100px; height: 100px;
    border-radius: 50%;
    background: var(--paper);
    display: flex; align-items: center; justify-content: center;
  }
  .footer-seal span {
    width: 62px; height: 62px;
    border-radius: 50%;
    border: 5px solid rgba(53,92,152,0.55);
  }
</style>
</head>
<body>
<main class="letterhead">
  <div class="icon-pattern" role="img" aria-label="Faint scattered line icons in brand colours: lightning bolts, light bulb, lock, map pin, chart and person outline"></div>

  <header class="brand">
    <span class="brand-dot"></span>
    <span class="brand-name">Parcelwise HQ</span>
  </header>

  <address class="address" style="font-style:normal">
    <div class="address-line">
      <svg width="14" height="14" viewBox="0 0 14 14" aria-hidden="true"><circle cx="7" cy="7" r="6" fill="none" stroke="#355c98" stroke-width="1.5"/><circle cx="7" cy="6" r="2" fill="#355c98"/></svg>
      42 Harbor Lane
    </div>
    <div class="address-line indent">Milltown, MI 48000</div>
  </address>

  <section class="letter-body">
    <p class="salutation">Dear Mr. Lorem,</p>
    <p class="copy">Lorem ipsum dolor sit amet, consectetuer adipiscing elit, sed diam nonummy nibh euismod tincidunt ut laoreet dolore magna aliquam erat volutpat. Ut wisi enim ad minim veniam, quis nostrud exerci tation ullamcorper suscipit lobortis nisl ut aliquip ex ea commodo consequat. Duis autem vel eum iriure dolor in hendiusto odio dignissim qui blandit praesent luptatum zzril delenit augue duis dolore te feugait nulla facilisi.</p>
    <p class="copy">Lorem ipsum dolor sit amet, consectetuer adipiscing elit, sed diam nonummy nibh euismod tincidunt ut laoreet dolore magna aliquam erat volutpat. Ut wisi enim ad minim veniam, quis nostrud exerci tation ullamcorper suscipit lobortis nisl ut aliquip ex ea commodo consequat. Duis autem vel eum iriure dolor in hendiusto odio dignissim qui blandit praesent luptatum zzril delenit augue duis dolore te feugait nulla facilisi.</p>
    <p class="copy">Lorem ipsum dolor sit amet, consectetuer adipiscing elit, sed diam nonummy nibh euismod tincidunt ut laoreet dolore magna aliquam erat volutpat. Ut wisi enim ad minim veniam, quis nostrud exerci tation ullamcorper suscipit lobortis nisl ut aliquip ex ea commodo consequat. Duis autem vel eum iriure dolor in hendiusto odio dignissim qui blandit praesent luptatum zzril delenit augue duis dolore te feugait nulla facilisi.</p>
    <p class="closing">Sincerely Your,</p>
    <p class="signature">Your Name</p>
  </section>

  <footer class="footer">
    <div class="footer-rule top"></div>
    <div class="footer-band">
      <span class="contact-item">
        <svg width="14" height="14" viewBox="0 0 14 14" aria-hidden="true"><circle cx="7" cy="7" r="6" fill="none" stroke="#fff" stroke-width="1.3"/><rect x="5" y="4" width="4" height="6" rx="1" fill="none" stroke="#fff" stroke-width="1.2"/></svg>
        (555) 014-2270
      </span>
      <span class="contact-item">
        <svg width="14" height="14" viewBox="0 0 14 14" aria-hidden="true"><path d="M3 2 L5.5 2 L6.5 5 L5 6 Q6.5 8.5 8 9 L9 7.5 L12 8.5 L12 11 Q6 12 3 2 Z" fill="none" stroke="#fff" stroke-width="1.2"/></svg>
        (555) 018-3300(Main)
      </span>
      <span class="contact-item">
        <svg width="14" height="14" viewBox="0 0 14 14" aria-hidden="true"><circle cx="7" cy="7" r="6" fill="none" stroke="#fff" stroke-width="1.3"/><rect x="3.8" y="4.8" width="6.4" height="4.4" fill="none" stroke="#fff" stroke-width="1.1"/><path d="M3.8 4.8 L7 7.3 L10.2 4.8" fill="none" stroke="#fff" stroke-width="1.1"/></svg>
        jsmith@parcelwisehq.example
      </span>
      <span class="contact-item">
        <svg width="14" height="14" viewBox="0 0 14 14" aria-hidden="true"><circle cx="7" cy="7" r="6" fill="none" stroke="#fff" stroke-width="1.3"/><ellipse cx="7" cy="7" rx="2.6" ry="6" fill="none" stroke="#fff" stroke-width="1.1"/><path d="M1 7 H13" stroke="#fff" stroke-width="1.1"/></svg>
        www.parcelwisehq.example
      </span>
    </div>
    <div class="footer-rule bottom"></div>
    <div class="footer-seal"><span></span></div>
  </footer>
</main>
</body>
</html>
```